Property Services Company Needs a Brochure Design

Looking for a new brochure design for an existing property services company.

We provide a range of property services from, market research, real estate brokerage, valuation and appraisal, property development and other real estate consulting services.

We would like a fresh modern brochure design with good graphics and features. Our colours are white, blue and orange.

The design should communicate, attention to detail, superior service delivery and distinction in results.
Updates

I would like the brochure to be roughly about 20 pages.

Containing the following,

1) An introduction
2) Contents Page
2) What we do
3) Our Services
4) Agency & Brokerage
5) Real Estate Consulting
6) Market Research
7) Appraisal & Valuation
8) Project Management
9) Property Development

I would also like icons to represent items 4,5,6,7,8 & 9, they should be represented vertically on each of the pages from the contents page and highlighted individually on the pages that they represent.. i.e. on appraisal & valuation page, all six icons will be arranged vertically and the appraisal and valuations icon will be highlighted.

I will also like to have images that depict the services on the various pages.

I have some pages I think will flow which I will upload shortly.

Industry/Entity Type

Real Estate

Font styles to use
Serif

Colors
f78f20
0455a3

```html
<!DOCTYPE html>
<html lang="en">
<head>
<meta charset="utf-8">
<title>What We Do – Brochure Spread</title>
<link href="https://fonts.googleapis.com/css2?family=Tinos:wght@400;700&display=swap" rel="stylesheet">
<style>
  :root {
    --backdrop: #e4e4e4;
    --paper: #f7f7f7;
    --orange: #e8762d;
    --purple: #4a3f80;
    --sky: #9cc4e4;
    --building-grey: #d4d4d6;
    --text-light: #fff4ea;
  }
  * { margin: 0; padding: 0; box-sizing: border-box; }
  html, body { width: 1200px; height: 720px; overflow: hidden; }
  body {
    background: var(--backdrop);
    font-family: "Tinos", "Times New Roman", serif;
  }
  .spread {
    position: absolute;
    left: 90px; top: 40px;
    width: 1020px; height: 640px;
    display: flex;
    box-shadow: 0 8px 24px rgba(0,0,0,0.12);
  }
  .page {
    position: relative;
    width: 510px; height: 640px;
    background: var(--paper);
    overflow: hidden;
  }
  .page--left { border-right: 1px solid #dcdcdc; }

  .rule { position: absolute; height: 4px; }
  .rule--purple { background: var(--purple); }
  .rule--orange { background: var(--orange); }

  .footer-band {
    position: absolute; left: 0; right: 0; bottom: 22px;
  }
  .footer-band .thin { height: 3px; background: var(--purple); margin-bottom: 5px; }
  .footer-band .thick { height: 10px; background: var(--orange); }

  .page-number {
    position: absolute; bottom: 50px;
    width: 26px; height: 24px;
    background: var(--purple); color: #fff;
    font-size: 13px; display: flex; align-items: center; justify-content: center;
  }

  .photo {
    position: absolute; left: 0; top: 40px;
    width: 510px; height: 270px;
    background: linear-gradient(160deg, var(--sky) 0%, #c8d9e6 55%, #8a9aa2 100%);
  }

  .section-title {
    position: absolute; left: 40px; top: 318px;
    color: var(--purple);
    font-size: 27px; font-weight: 400; letter-spacing: 0.5px;
    line-height: 1;
  }

  .text-panel {
    position: absolute;
    background: var(--orange);
    color: var(--text-light);
    font-size: 11px; line-height: 1.45;
  }
  .text-panel p + p { margin-top: 8px; }
  .text-panel--intro { left: 170px; top: 356px; width: 340px; padding: 20px 24px 20px 26px; }
  .text-panel--growth { left: 40px; top: 140px; width: 310px; padding: 22px 22px; }

  .building-mark {
    position: absolute; right: 40px; top: 50px;
    width: 70px; height: 110px;
    background: linear-gradient(180deg, #e6e6e8, var(--building-grey));
  }
</style>
</head>
<body>
  <div class="spread">
    <section class="page page--left">
      <div class="rule rule--purple" style="left:250px; top:14px; width:170px;"></div>
      <div class="rule rule--orange" style="left:430px; top:14px; width:80px;"></div>
      <div class="photo" role="img" aria-label="Photo of three construction workers in hard hats and safety vests reviewing building plans on site"></div>
      <h1 class="section-title">WHAT WE DO</h1>
      <div class="text-panel text-panel--intro">
        <p>Harrowgate is a leading property services company incorporated in 1984, providing bespoke solutions in advisory, brokerage and turnkey solutions to owners, occupiers and property investors. Over the years we have expanded our services with a foundation based on core strengths, unrivalled local expertise, network and knowledge combined with strategic partnerships. As well as providing property solutions we also develop commercial and residential units.</p>
      </div>
      <div class="page-number" style="left:30px;">3</div>
      <div class="footer-band"><div class="thin"></div><div class="thick"></div></div>
    </section>

    <section class="page page--right">
      <div class="rule rule--orange" style="left:0; top:30px; width:90px;"></div>
      <div class="rule rule--purple" style="left:100px; top:30px; width:180px;"></div>
      <div class="building-mark" role="img" aria-label="Grey illustration of office towers"></div>
      <div class="text-panel text-panel--growth">
        <p>Our growth has been based on maintaining relationships with our extensive client base, ranging from financial institutions, government agencies, airlines and servicing companies, manufacturing companies, multinationals and local corporations, to private developers and investors. Our clients depend on our ability to draw on years of experience in the local market; our professionals know their communities and the property market inside and out, and provide knowledgeable, creative solutions to all their real estate needs.</p>
        <p>The combination of our integrated services allows us to provide a superior end to end solution to our clients, customised to their own requirements. Market research is a core component to our business model, allowing us to make informed decisions based on our research findings. Our brokerage teams also benefit from this information, allowing our associates to advise clients on how best to maximise return on their investment on the sale or buy side within a short timeframe.</p>
        <p>We pay great attention to detail and consideration of our clients' requirements, delivering mandates with distinction.</p>
      </div>
      <div class="page-number" style="right:30px;">4</div>
      <div class="footer-band"><div class="thin"></div><div class="thick"></div></div>
    </section>
  </div>
</body>
</html>
```